Nanotechnology meets nature cosmetic company needs label design. Name of the company is BriolaGrove

We are a cosmetic brand that combines nanotechnology with nature in the form of hemp extracts and essential oils, creating products that provide pain relief as well as stress reduction and relaxation. We have three different products and need three separate labels. We have a logo and would like to incorporate that into the label design. The colors are teal, black and gray. We would like to convey a message of combining nature with cutting edge cosmetic technology.
1. Topical pain lotion
2. Bath soak
3. Massage lotion
The logo is attached and I would just like the logo used and not the text below. The colors of the logo should be teal cross and "V" inside the gray lines that make up the circle with black color inside the circle. If this can't be done, I can send another logo.

```html
<!DOCTYPE html>
<html lang="en">
<head>
<meta charset="utf-8">
<title>BriolaGrove Muscles &amp; Joints Label</title>
<link rel="stylesheet" href="https://fonts.googleapis.com/css2?family=Poppins:wght@300;400;600;700;800&display=swap">
<style>
  :root {
    --page-bg: #f3f4f5;
    --label-black: #1a1a1a;
    --label-black-soft: #2a2a2a;
    --teal: #1fbfa8;
    --teal-deep: #14a893;
    --gray-ring: #8c8c8c;
    --white: #ffffff;
    --art-blue: #1d5a8a;
    --art-dark: #141a22;
  }
  * { margin: 0; padding: 0; box-sizing: border-box; }
  html, body {
    width: 1083px; height: 1200px; overflow: hidden;
    background: var(--page-bg);
    font-family: "Poppins", sans-serif;
  }
  .label {
    position: absolute; left: 327px; top: 72px;
    width: 428px; height: 1055px;
    background: linear-gradient(90deg, var(--label-black) 0%, var(--label-black-soft) 50%, var(--label-black) 100%);
    overflow: hidden;
  }
  .brand-mark {
    position: absolute; left: 104px; top: 90px;
    width: 210px; height: 210px; border-radius: 50%;
    border: 6px solid var(--gray-ring);
    background: #000;
    display: flex; align-items: center; justify-content: center;
  }
  .brand-name {
    font-family: "Poppins", sans-serif;
    font-weight: 600; font-size: 30px; color: var(--teal);
    letter-spacing: 0.5px;
  }
  .headline { position: absolute; left: 14px; top: 325px; width: 400px; height: 280px; }
  .headline text { font-family: "Poppins", sans-serif; }
  .tagline {
    position: absolute; left: 14px; top: 612px; width: 400px;
    font-weight: 300; font-size: 27px; color: var(--white);
    letter-spacing: -0.3px; white-space: nowrap;
  }
  .art-runner {
    position: absolute; left: 185px; top: 690px; width: 232px; height: 290px;
    background: radial-gradient(ellipse at 55% 45%, var(--art-blue) 0%, #16344f 45%, var(--art-dark) 80%, transparent 100%);
    border-radius: 8px;
  }
  .ingredients {
    position: absolute; left: 14px; top: 698px; width: 170px;
    font-weight: 300; font-size: 21px; line-height: 28px; color: var(--teal);
  }
  .benefits {
    position: absolute; left: 14px; top: 872px; list-style: none;
  }
  .benefits li {
    font-weight: 600; font-size: 18px; color: var(--white);
    height: 38px; line-height: 38px; white-space: nowrap;
  }
  .benefits li::before { content: "\2022"; margin-right: 4px; font-size: 12px; vertical-align: top; }
  .net-band {
    position: absolute; left: 0; bottom: 0; width: 100%; height: 53px;
    background: linear-gradient(90deg, var(--teal-deep), var(--teal));
    display: flex; align-items: center; padding-left: 14px;
  }
  .net-weight { font-weight: 300; font-size: 26px; color: var(--white); }
</style>
</head>
<body>
  <main class="label">
    <div class="brand-mark"><span class="brand-name">BriolaGrove</span></div>

    <svg class="headline" viewBox="0 0 400 280" aria-label="Calm Current Muscles &amp; Joints">
      <text x="0" y="72" font-size="84" font-weight="600" fill="#1fbfa8" textLength="400" lengthAdjust="spacingAndGlyphs">CALM CURRENT</text>
      <text x="0" y="171" font-size="100" font-weight="700" fill="#ffffff" textLength="400" lengthAdjust="spacingAndGlyphs">MUSCLES</text>
      <text x="0" y="268" font-size="100" font-weight="700" fill="#ffffff" textLength="400" lengthAdjust="spacingAndGlyphs">&amp; JOINTS</text>
    </svg>

    <p class="tagline">Nanotechnology meets nature</p>

    <div class="art-runner" role="img" aria-label="Glowing blue anatomical runner figure with highlighted joints"></div>

    <p class="ingredients">Made with<br>hemp-based<br>cannabinoids<br>and other fruits<br>of nature</p>

    <ul class="benefits">
      <li>Fast Acting</li>
      <li>Non-Greasy</li>
      <li>Plant-Based Ingredients</li>
    </ul>

    <div class="net-band"><span class="net-weight">Net wt. 4oz. (113.4g)</span></div>
  </main>
</body>
</html>
```